Business Card for a mobile physiotherapy company

I need a layout for a business card for a mobile physiotherapy company.
Slogan is "Mobile Physiotherapy - Your Road To Recovery"
Phone number is 867-555-0142
Email VardenTherapy@postnest.ca (subject to change with website)
Website www.VardenTherapy.ca
My name and credentials: Luke Varden Luke Varden, BSc(kin), MPT, CAFCI, IMS
Information maybe included: Direct Billing, Services including Physiotherapy, IMS, acupuncture
Maybe include facebook and instagram logos
One side with the logo clean and sharp
Other side with details, try not to look too busy, keep everything concise

```html
<!DOCTYPE html>
<html lang="en">
<head>
<meta charset="utf-8">
<title>Varden Therapy – Business Card</title>
<link rel="stylesheet" href="https://fonts.googleapis.com/css2?family=Merriweather:wght@300;400;700&display=swap">
<style>
  :root {
    --navy: #24416b;
    --teal: #1c5a57;
    --green: #15584a;
    --paper: #f4f4f2;
    --stage: #d6d6d6;
    --ink-soft: #3f4f63;
    --white: #ffffff;
  }
  * { margin: 0; padding: 0; box-sizing: border-box; }
  html, body { width: 1200px; height: 576px; overflow: hidden; }
  body {
    background: var(--stage);
    font-family: "Merriweather", Georgia, serif;
    position: relative;
  }
  .card {
    position: absolute;
    top: 138px;
    width: 484px;
    height: 293px;
    border-radius: 14px;
    overflow: hidden;
  }

  /* Front */
  .card--front {
    left: 82px;
    background: linear-gradient(120deg, var(--teal) 0%, #22486a 55%, var(--navy) 100%);
    color: var(--white);
    text-align: center;
  }
  .brand-front__mark {
    position: absolute; left: 192px; top: 62px;
    width: 100px; height: 100px; border-radius: 50%;
    background: rgba(255, 255, 255, 0.07);
  }
  .brand-front__name {
    position: absolute; left: 0; right: 0; top: 140px;
    font-weight: 700; font-size: 40px; line-height: 1; color: var(--white);
  }
  .brand-front__rule {
    position: absolute; left: 111px; top: 195px;
    width: 262px; height: 2px; background: var(--white);
  }
  .brand-front__slogan {
    position: absolute; left: 0; right: 0; top: 199px;
    font-weight: 300; font-size: 10.5px; letter-spacing: .2px;
  }
  .services {
    position: absolute; left: 0; right: 0; top: 263px;
    font-weight: 300; font-size: 12px; letter-spacing: .2px;
  }
  .services span { margin: 0 6px; }

  /* Back */
  .card--back { left: 602px; width: 480px; background: var(--paper); color: var(--navy); }
  .wave { position: absolute; left: 0; top: 0; }
  .tagline {
    position: absolute; right: 25px; top: 17px;
    color: var(--white); font-weight: 300; font-size: 12px; line-height: 1.4; text-align: right;
  }
  .brand-back { position: absolute; left: 30px; top: 66px; width: 200px; text-align: center; }
  .brand-back__mark {
    width: 90px; height: 90px; border-radius: 50%;
    background: var(--navy); margin: 0 auto;
  }
  .brand-back__name {
    color: var(--green); font-weight: 700; font-size: 25px; line-height: 1; margin-top: 14px;
  }
  .follow {
    position: absolute; left: 48px; top: 247px;
    display: flex; align-items: center; gap: 6px;
    font-weight: 300; font-size: 12px; color: var(--ink-soft);
  }
  .follow__dot { width: 19px; height: 19px; border-radius: 50%; background: var(--navy); }
  .follow__dot--alt { background: var(--green); }
  .person { position: absolute; right: 25px; top: 143px; text-align: right; }
  .person__name { font-weight: 700; font-size: 19px; letter-spacing: .5px; }
  .person__cred { font-weight: 300; font-size: 10.5px; color: var(--ink-soft); margin-top: 5px; }
  .contact { position: absolute; right: 25px; top: 216px; list-style: none; text-align: right; }
  .contact li {
    display: flex; justify-content: flex-end; align-items: center; gap: 8px;
    font-weight: 400; font-size: 12.5px; line-height: 17.5px; color: var(--navy);
  }
  .contact svg { width: 10px; height: 10px; fill: var(--green); }
</style>
</head>
<body>

<section class="card card--front" aria-label="Card front">
  <div class="brand-front__mark" aria-hidden="true"></div>
  <div class="brand-front__name">Varden Therapy</div>
  <div class="brand-front__rule"></div>
  <div class="brand-front__slogan">Mobile Physiotherapy - Your Road To Recovery</div>
  <p class="services">Direct Billing<span>|</span>Services Including Physiotherapy<span>|</span>IMS<span>|</span>Acupuncture</p>
</section>

<section class="card card--back" aria-label="Card back">
  <svg class="wave" width="480" height="120" viewBox="0 0 480 120" aria-hidden="true">
    <path d="M0,0 H480 V72 C410,92 330,82 250,52 C175,22 80,14 0,46 Z" fill="#24416b"/>
    <path d="M0,68 C70,32 160,26 240,56 C320,86 410,100 480,80" fill="none" stroke="#15584a" stroke-width="9"/>
    <path d="M0,57 C70,22 160,16 240,46 C320,76 410,90 480,71" fill="none" stroke="#f4f4f2" stroke-width="5"/>
  </svg>
  <p class="tagline">Mobile Physiotherapy<br>Your Road To Recovery</p>

  <div class="brand-back">
    <div class="brand-back__mark" aria-hidden="true"></div>
    <div class="brand-back__name">Varden Therapy</div>
  </div>

  <div class="follow">
    <span>Follow us on:</span>
    <span class="follow__dot"></span>
    <span class="follow__dot follow__dot--alt"></span>
  </div>

  <div class="person">
    <div class="person__name">LUKE VARDEN</div>
    <div class="person__cred">BSc(kin), MPT, CAFCI, IMS</div>
  </div>

  <ul class="contact">
    <li>867-555-0142
      <svg viewBox="0 0 10 10" aria-hidden="true"><path d="M2.2,0.6 L3.6,2.6 L2.8,3.6 C3.4,5 4.8,6.4 6.3,7.1 L7.3,6.3 L9.4,7.6 L8.6,9.4 C4.5,9.6 0.4,5.5 0.6,1.4 Z"/></svg>
    </li>
    <li>VardenTherapy@postnest.ca
      <svg viewBox="0 0 10 10" aria-hidden="true"><path d="M0,2 H10 V8.5 H0 Z M0.6,2.4 L5,5.8 L9.4,2.4" stroke="#f4f4f2" stroke-width=".7"/></svg>
    </li>
    <li>www.VardenTherapy.ca
      <svg viewBox="0 0 10 10" aria-hidden="true"><circle cx="5" cy="5" r="4.6"/><path d="M0.6,5 H9.4 M5,0.4 V9.6 M5,0.6 C2.6,3 2.6,7 5,9.4 M5,0.6 C7.4,3 7.4,7 5,9.4" stroke="#f4f4f2" stroke-width=".6" fill="none"/></svg>
    </li>
  </ul>
</section>

</body>
</html>
```